Plum Lantern Cannabis Cartridge box

Box with both inside and outside box. A disposable cannabis vape cart is the contents of the package. initial thoughts were black exterior box with color highlight. (example of Jiva gum attached). There are four colors currently being used for the actual product. Black, White, Green and Blue. product will sit in retail display box. It should both "pop" and still emote quality and class.

Target Market(s)

Professional, discreet cannabis consumer. Experienced and knowledgeable

Industry/Entity Type

Cannabis

Font styles to use
Serif

Colors

Designer to choose colors to be used in the design.

Requirements
Must have
• use logo and logo colors
Nice to have
• elegant look. metalic foil printing, embossing available

```html
<!DOCTYPE html>
<html lang="en">
<head>
<meta charset="utf-8">
<title>Plum Lantern – Cartridge Box Dieline</title>
<link rel="stylesheet" href="https://fonts.googleapis.com/css2?family=Cinzel:wght@700&display=swap">
<style>
  :root {
    --paper: #ffffff;
    --panel-light: #f7f7f7;
    --panel-dark: #121212;
    --brand-green: #14a085;
    --band-blue: #0072bc;
    --band-indigo: #2e3192;
    --band-sky: #0a8fd0;
    --dieline: #e0332b;
  }
  html, body {
    margin: 0;
    padding: 0;
    width: 840px;
    height: 1200px;
    overflow: hidden;
    background: var(--paper);
  }
  .box-dieline {
    display: block;
    width: 840px;
    height: 1200px;
  }
  .panel-base { fill: var(--panel-light); }
  .panel-dark { fill: var(--panel-dark); }
  .cut-line, .fold-line {
    fill: none;
    stroke: var(--dieline);
    stroke-width: 1.4;
  }
  .hang-hole {
    fill: var(--paper);
    stroke: var(--dieline);
    stroke-width: 1.4;
  }
  .brand-name {
    font-family: "Cinzel", serif;
    font-weight: 700;
    fill: var(--brand-green);
    text-anchor: middle;
    letter-spacing: 2px;
  }
</style>
</head>
<body>
<svg class="box-dieline" viewBox="0 0 1500 2142" xmlns="http://www.w3.org/2000/svg">
  <defs>
    <clipPath id="box-shape">
      <path id="box-outline-path" d="M590,228 H910 Q933,228 933,250 V350 L938,360 V425 H1075 Q1090,425 1095,440 L1118,518 L1135,537 H1220 Q1242,537 1242,560 V1582 Q1242,1605 1220,1605 H1135 L1118,1625 L1095,1700 Q1090,1715 1075,1715 H938 V1780 L933,1790 V1890 Q933,1912 910,1912 H590 Q567,1912 567,1890 V1790 L562,1780 V1715 H425 Q410,1715 405,1700 L382,1625 L365,1605 H280 Q258,1605 258,1582 V560 Q258,537 280,537 H365 L382,518 L405,440 Q410,425 425,425 H562 V360 L567,350 V250 Q567,228 590,228 Z"/>
    </clipPath>
    <linearGradient id="band-gradient" x1="258" y1="0" x2="1242" y2="0" gradientUnits="userSpaceOnUse">
      <stop offset="0" stop-color="var(--band-blue)"/>
      <stop offset="0.25" stop-color="var(--band-indigo)"/>
      <stop offset="0.45" stop-color="var(--band-sky)"/>
      <stop offset="0.68" stop-color="var(--band-indigo)"/>
      <stop offset="0.85" stop-color="var(--band-blue)"/>
      <stop offset="1" stop-color="var(--band-sky)"/>
    </linearGradient>
  </defs>

  <g class="box-artwork" clip-path="url(#box-shape)">
    <rect class="panel-base" x="0" y="0" width="1500" height="2142" role="img" aria-label="Light panel area with faint hexagon texture"/>
    <path class="accent-band" fill="url(#band-gradient)"
      d="M258,615 C430,880 720,1250 950,1400 C1050,1460 1080,1350 1090,1200 C1100,1050 1150,925 1242,935 V2000 H258 Z"/>
    <path class="panel-dark" role="img" aria-label="Black panel area with dark hexagon texture"
      d="M258,845 C520,1130 780,1380 960,1470 C1060,1510 1085,1420 1095,1250 C1110,1080 1170,1000 1242,1000 V2000 H258 Z"/>
  </g>

  <g class="dieline">
    <use href="#box-outline-path" class="cut-line"/>
    <rect class="fold-line" x="591" y="252" width="317" height="120"/>
    <line class="fold-line" x1="588" y1="385" x2="912" y2="385"/>
    <path class="fold-line" d="M402,550 L430,450 H545 L583,540"/>
    <path class="fold-line" d="M1098,550 L1070,450 H955 L917,540"/>
    <rect class="fold-line" x="284" y="562" width="932" height="1018"/>
    <line class="fold-line" x1="402" y1="550" x2="402" y2="1590"/>
    <rect class="fold-line" x="416" y="550" width="667" height="1040"/>
    <line class="fold-line" x1="583" y1="540" x2="583" y2="1600"/>
    <line class="fold-line" x1="917" y1="540" x2="917" y2="1600"/>
    <line class="fold-line" x1="1098" y1="550" x2="1098" y2="1590"/>
    <path class="fold-line" d="M402,1590 L430,1690 H545 L583,1600"/>
    <path class="fold-line" d="M1098,1590 L1070,1690 H955 L917,1600"/>
    <line class="fold-line" x1="588" y1="1755" x2="912" y2="1755"/>
    <rect class="fold-line" x="591" y="1768" width="317" height="120"/>
    <circle class="hang-hole" cx="1000" cy="1385" r="48"/>
  </g>

  <g class="front-brand">
    <text class="brand-name" x="750" y="850" font-size="88">Plum</text>
    <text class="brand-name" x="750" y="950" font-size="70">Lantern</text>
  </g>
  <g class="side-brand">
    <text class="brand-name" x="505" y="1440" font-size="50">Plum</text>
    <text class="brand-name" x="505" y="1500" font-size="38">Lantern</text>
  </g>
</svg>
</body>
</html>
```